Business Card for Coastal Tundrabridge Advisory

We need a business card for Coastal Tundrabridge Advisory. The company website address is provided below. The company logo is attached. We provide specialized permafrost services to the mining, transportation, and oil & gas industries. The card should be prepared for:
Matthias Korhonen, PhD.
Coastal Tundrabridge Advisory
PO Box 418259
Quillwater, Alaska 99642
Direct: +1-907-555-0143
Email: mkorhonen@tundrabridgeadvisory.example
Website: www.coastaltundrabridgeadvisory.example

```html
<!DOCTYPE html>
<html lang="en">
<head>
<meta charset="utf-8">
<title>Coastal Tundrabridge Advisory – Business Card</title>
<link href="https://fonts.googleapis.com/css2?family=Montserrat:wght@400;500;600;700&display=swap" rel="stylesheet">
<style>
  :root {
    --page-bg: #e9e7e3;
    --card-white: #ffffff;
    --ink: #111a22;
    --ink-soft: #2b333b;
    --band: #111a22;
    --band-text: #e8ecef;
    --back-bg: #0f171f;
    --pattern-light: #4a5058;
    --pattern-dark: #0b1116;
  }
  * { margin: 0; padding: 0; box-sizing: border-box; }
  html, body { width: 900px; height: 1200px; overflow: hidden; }
  body {
    position: relative;
    background: var(--page-bg);
    font-family: "Montserrat", Arial, sans-serif;
    color: var(--ink);
  }
  .card {
    position: absolute;
    left: 80px;
    width: 742px;
    height: 440px;
    border-radius: 22px;
    overflow: hidden;
    box-shadow: 0 10px 24px rgba(0,0,0,0.18);
  }
  /* Front */
  .card-front { top: 131px; background: var(--card-white); }
  .front-brand {
    position: absolute;
    left: 52px; top: 218px;
    width: 258px;
    font-weight: 700;
    font-size: 20px;
    line-height: 24px;
    letter-spacing: 1px;
    text-transform: uppercase;
    color: var(--ink);
    text-align: center;
  }
  .divider {
    position: absolute;
    left: 316px; top: 161px;
    width: 2px; height: 143px;
    background: var(--ink);
  }
  .person { position: absolute; left: 328px; top: 157px; }
  .person-name { font-size: 22px; font-weight: 700; line-height: 28px; color: var(--ink); }
  .person-title { font-size: 15.5px; font-weight: 500; line-height: 22px; color: var(--ink-soft); }
  .contacts { position: absolute; left: 330px; top: 219px; list-style: none; }
  .contact {
    display: flex; align-items: center;
    height: 31px;
    font-size: 15.5px; font-weight: 500;
    color: var(--ink);
  }
  .contact svg { width: 16px; height: 16px; margin-right: 14px; flex: none; }
  .address-band {
    position: absolute;
    left: 0; top: 369px;
    width: 100%; height: 53px;
    background: var(--band);
    color: var(--band-text);
    font-size: 16px;
    display: flex; align-items: center; justify-content: center;
  }
  /* Back */
  .card-back { top: 638px; background: var(--back-bg); }
  .back-pattern {
    position: absolute; inset: 0;
    background: linear-gradient(135deg, var(--pattern-light) 0%, #23292f 35%, var(--pattern-dark) 70%);
    opacity: 0.55;
  }
  .back-brand {
    position: absolute;
    left: 0; right: 0; top: 340px;
    text-align: center;
    font-weight: 700;
    font-size: 20px;
    letter-spacing: 1px;
    text-transform: uppercase;
    color: #ffffff;
  }
</style>
</head>
<body>
  <section class="card card-front">
    <div class="front-brand">Coastal Tundrabridge Advisory</div>
    <div class="divider"></div>
    <div class="person">
      <div class="person-name">Matthias Korhonen, PhD.</div>
      <div class="person-title">Managing Director</div>
    </div>
    <ul class="contacts">
      <li class="contact">
        <svg viewBox="0 0 24 24" aria-hidden="true"><path fill="none" stroke="#111a22" stroke-width="2" d="M5 3h4l2 5-2.5 1.5a11 11 0 0 0 6 6L16 13l5 2v4a2 2 0 0 1-2 2A16 16 0 0 1 3 5a2 2 0 0 1 2-2z"/></svg>
        +1-907-555-0143
      </li>
      <li class="contact">
        <svg viewBox="0 0 24 24" aria-hidden="true"><rect x="3" y="6" width="18" height="12" rx="1" fill="#111a22"/><path d="M3 7l9 6 9-6" fill="none" stroke="#fff" stroke-width="1.6"/></svg>
        mkorhonen@tundrabridgeadvisory.example
      </li>
      <li class="contact">
        <svg viewBox="0 0 24 24" aria-hidden="true"><circle cx="12" cy="12" r="9" fill="none" stroke="#111a22" stroke-width="2"/><path d="M3 12h18M12 3c3 3 3 15 0 18M12 3c-3 3-3 15 0 18" fill="none" stroke="#111a22" stroke-width="1.6"/></svg>
        www.coastaltundrabridgeadvisory.example
      </li>
    </ul>
    <div class="address-band">PO Box 418259 Quillwater, Alaska 99642</div>
  </section>

  <section class="card card-back">
    <div class="back-pattern" role="img" aria-label="Repeated faint company name pattern across the back of the card"></div>
    <div class="back-brand">Coastal Tundrabridge Advisory</div>
  </section>
</body>
</html>
```